PillPeak website blog. Simple medical advice given in clear yes or no answers that save people money

I am developing a new web page that provides medical care cost savings at the consumers' fingertips. I need a web page that is clean, concise, and attractive for me to put my valuable medical information on. The information I provide is simple to obtain, yet very valuable to the consumer, and answered in a yes or no format. For example, A person may wonder if they need an antibiotic for cold like symptoms. Seeing a doctor for an antibiotic is very expensive. But with simple and clear advice at their fingertips, they can confidently avoid having to pay $200 or more to see a doctor and get an antibiotic. This is kind of like consumer reports for medical services.

Target Market(s)

People who are savvy shoppers and want to save money on healthcare. Likely younger ages between 21 and 60, who are mobile, readily use iphones, and want strong evidence based research to guide their decisions.

Industry/Entity Type

Coding

Number of Pages Required

Colors

Requirements
Must have
• A template on the "Question" and "Answer" page that can be edited many times that can be edited many times. The Confidence rating scale would need to be edited as well. The "Date Researched" the "PillPeak Pilluminate" and "References" all need to be able to be edited. This website must be very clear and simple to understand. A medical question is posed with a yes or no answer, then answered and given a confidence rating, we then tell them how much money they saved by going to our website.
Nice to have
• We want this to be slightly fun, vibrant, warm and inviting. This will be sometime later converted into an app format. Quirky, some humor to keep it interesting.
Should not have
• No sterile looking medical images. Not boring.

```html
<!DOCTYPE html>
<html lang="en">
<head>
<meta charset="utf-8">
<title>PillPeak — Clear Valuable Health Advice</title>
<link rel="stylesheet" href="https://fonts.googleapis.com/css2?family=Cinzel:wght@400;600;700&family=Open+Sans:ital,wght@0,400;0,600;1,400&display=swap">
<style>
:root{
  --blue:#1560b0;
  --blue-dark:#0f4f95;
  --red:#e2001f;
  --red-dark:#b80018;
  --ink:#2f2f2f;
  --grey:#6c6c6c;
  --line:#d6d6d6;
  --footer:#141414;
  --white:#ffffff;
}
*{box-sizing:border-box;margin:0;padding:0}
html,body{width:1144px;height:1200px;overflow:hidden;background:var(--white)}
body{position:relative;font-family:"Open Sans",sans-serif;color:var(--ink)}
.abs{position:absolute}

/* header */
.brand{left:165px;top:18px;width:140px;height:96px;display:flex;flex-direction:column;align-items:center;justify-content:flex-end}
.brand-dot{width:58px;height:58px;border-radius:50%;background:var(--blue);margin-bottom:6px}
.brand-name{font-family:"Cinzel",serif;font-weight:700;font-size:25px;color:var(--blue);line-height:1}
.tagline{left:373px;top:46px;font-family:"Cinzel",serif;font-weight:600;font-size:23px;color:#333;letter-spacing:.3px;white-space:nowrap}

/* nav */
.main-nav{left:0;top:124px;width:1144px;height:50px;background:var(--blue)}
.main-nav svg{position:absolute;left:0;top:0}
.nav-item{position:absolute;top:0;height:50px;line-height:50px;font-family:"Cinzel",serif;font-weight:600;font-size:13px;color:var(--white);letter-spacing:.4px;white-space:nowrap}

/* search */
.search{left:165px;top:188px;width:813px;height:35px;border:1px solid var(--line);border-radius:2px}
.search-field{position:absolute;left:8px;top:0;line-height:33px;font-style:italic;font-size:11px;color:#333}
.search-btn{position:absolute;right:-1px;top:-1px;width:81px;height:35px;background:var(--red);color:var(--white);font-family:"Cinzel",serif;font-weight:600;font-size:12px;display:flex;align-items:center;justify-content:center;gap:5px}

/* hero */
.hero{left:0;top:236px;width:1144px;height:479px;overflow:hidden}
.hero-art{position:absolute;inset:0;background:
  radial-gradient(ellipse 420px 300px at 640px 280px,rgba(120,150,220,.55),transparent 70%),
  radial-gradient(ellipse 420px 300px at 80px 460px,rgba(70,170,190,.75),transparent 70%),
  linear-gradient(100deg,#0d1a3a 0%,#162a5e 40%,#3a4f9c 65%,#1a2552 100%)}
.side-menu{position:absolute;left:0;top:74px;width:262px;background:var(--red);border-left:4px solid var(--red-dark);box-shadow:2px 2px 6px rgba(0,0,0,.3)}
.side-menu li{list-style:none;height:47.4px;line-height:47.4px;padding-left:12px;font-family:"Cinzel",serif;font-weight:600;font-size:16px;color:var(--white);border-bottom:1px solid rgba(0,0,0,.12)}
.side-menu li:last-child{border-bottom:none}
.hero-copy{position:absolute;left:645px;top:174px;font-family:"Cinzel",serif;font-weight:700;color:var(--white);line-height:1.25;text-shadow:0 1px 4px rgba(0,0,0,.4)}
.hero-copy .small{font-size:27px}
.hero-copy .big{font-size:35px}
.dots{position:absolute;left:937px;top:419px;display:flex;gap:4px}
.dots span{width:11px;height:11px;border-radius:50%;background:var(--white)}
.dots .on{border:3px solid var(--white);background:var(--red)}

/* join */
.section-title{left:0;width:1144px;text-align:center;font-family:"Cinzel",serif;font-weight:600;font-size:26px;color:#333}
.section-title em{font-style:normal;color:var(--blue)}
.join-form{left:330px;top:823px;width:485px;height:44px;border:1px solid var(--line)}
.join-field{position:absolute;left:15px;top:0;line-height:42px;font-family:"Cinzel",serif;font-size:11px;color:#555}
.join-btn{position:absolute;right:-1px;top:-1px;width:87px;height:44px;background:var(--red);color:var(--white);font-family:"Cinzel",serif;font-weight:700;font-size:14px;display:flex;align-items:center;justify-content:center}

/* footer */
.footer{left:0;top:972px;width:1144px;height:228px;background:linear-gradient(180deg,#1b1b1b,var(--footer) 60%,#0b0b0b)}
.footer-notch{position:absolute;left:0;top:0}
.ask-row{left:0;top:969px;width:1144px;display:flex;justify-content:center;align-items:center;gap:8px}
.ask-lead{font-family:"Cinzel",serif;font-size:15px;letter-spacing:5px;color:#555}
.ask-btn{width:160px;height:44px;background:var(--blue);color:var(--white);font-family:"Cinzel",serif;font-weight:700;font-size:16px;display:flex;align-items:center;justify-content:center}
.disclaimer{left:165px;top:1074px;width:780px;display:flex;gap:8px}
.disclaimer-label{font-family:"Cinzel",serif;font-weight:600;font-size:13px;color:var(--white);white-space:nowrap;line-height:19px}
.disclaimer p{font-size:10.5px;line-height:19px;color:#ddd}
.footer-rule{left:165px;top:1144px;width:813px;height:1px;background:#333}
.copyright{left:165px;top:1166px;font-size:10.5px;color:#ddd}
.social{left:872px;top:1167px;display:flex;gap:17px}
.social span{width:14px;height:14px;border-radius:50%;background:#e6e6e6}
</style>
</head>
<body>

<header>
  <div class="abs brand"><span class="brand-dot"></span><span class="brand-name">PillPeak</span></div>
  <div class="abs tagline">Clear Valuable. Health. Advice. Right Now</div>
</header>

<nav class="abs main-nav">
  <svg width="1144" height="50" aria-hidden="true">
    <g stroke="#3d7cc4" stroke-width="1">
      <line x1="172" y1="50" x2="180" y2="0"/><line x1="318" y1="50" x2="332" y2="0"/>
      <line x1="482" y1="50" x2="496" y2="0"/><line x1="630" y1="50" x2="644" y2="0"/>
      <line x1="704" y1="50" x2="718" y2="0"/><line x1="808" y1="50" x2="822" y2="0"/>
      <line x1="876" y1="50" x2="890" y2="0"/><line x1="960" y1="50" x2="974" y2="0"/>
    </g>
  </svg>
  <span class="nav-item" style="left:185px">Prev / Screening</span>
  <span class="nav-item" style="left:349px">Women's Health</span>
  <span class="nav-item" style="left:513px">Men's Health</span>
  <span class="nav-item" style="left:652px">Meds</span>
  <span class="nav-item" style="left:734px">Imaging</span>
  <span class="nav-item" style="left:833px">Peds</span>
  <span class="nav-item" style="left:909px">Clinic</span>
</nav>

<div class="abs search">
  <span class="search-field">Enter Keyword</span>
  <span class="search-btn">
    <svg width="10" height="10" viewBox="0 0 10 10" aria-hidden="true"><circle cx="4" cy="4" r="3" fill="none" stroke="#fff" stroke-width="1.6"/><line x1="6.2" y1="6.2" x2="9.3" y2="9.3" stroke="#fff" stroke-width="1.8"/></svg>
    Search
  </span>
</div>

<section class="abs hero">
  <div class="hero-art" role="img" aria-label="Blue medical-themed background with glowing hexagons and soft light"></div>
  <ul class="side-menu">
    <li>Who We Are?</li>
    <li>How It Works</li>
    <li>How We Know</li>
    <li>Evidence Based Research</li>
    <li>Dr. Whitlow</li>
    <li>Who We Are Not</li>
    <li>Are We Biased?</li>
  </ul>
  <div class="hero-copy">
    <div class="small">Save $ 1,000 Per Year</div>
    <div class="big">On Healthcare.</div>
    <div class="big">It's Free!</div>
  </div>
  <div class="dots"><span></span><span class="on"></span><span></span></div>
</section>

<h2 class="abs section-title" style="top:766px">Become A <em>PillPeak</em> Today!</h2>
<div class="abs join-form">
  <span class="join-field">Enter Email:</span>
  <span class="join-btn">Submit</span>
</div>

<h2 class="abs section-title" style="top:922px">Ask A Question Here!</h2>

<footer class="abs footer">
  <svg class="footer-notch" width="1144" height="62" aria-hidden="true">
    <polygon points="165,0 978,0 905,62 239,62" fill="#ffffff"/>
  </svg>
</footer>
<div class="abs ask-row">
  <span class="ask-lead">If it is worthy,</span>
  <span class="ask-btn">Well Post It!</span>
</div>

<div class="abs disclaimer">
  <span class="disclaimer-label">Disclaimer:</span>
  <p>Lorem ipsum dolor sit amet, consectetur adipiscing elit, sed do eiusmod tempor incididunt ut labore et dolore magna aliqua. Ut enim ad minim veniam, quis nostrud exercitation ullamco laboris nisi ut aliquip ex ea commodo conscing elit, sed do eiusmod tempor inciequat.</p>
</div>
<div class="abs footer-rule"></div>
<div class="abs copyright">© 2018 PillPeak. All Rights Are Reserved.Terms of Use | Privacy Policy</div>
<div class="abs social" aria-label="Social links"><span></span><span></span><span></span><span></span></div>

</body>
</html>
```